Packaging design for a reclosable bag for our product

We have a logo, and we need to put it on packaging for our product and while we want the look to be simple, we want it to follow good design principles and also contain spaces for other product descriptions.

There will be 5 sizes at launch so I'd like 5 variations, one for each size.

I've included a few mockups of the type of bag that I made but they are all just rough ideas that I had.

I want the brand to look scientific and methodical and even a bit quirky, as in "wow this is a serious product but also a bit unusual."

```html
<!DOCTYPE html>
<html lang="en">
<head>
<meta charset="UTF-8">
<title>Lumora Bias Lighting – Extra Large Pack</title>
<link rel="stylesheet" href="https://fonts.googleapis.com/css2?family=Tinos:wght@400;700&display=swap">
<style>
  :root {
    --pack-black: #000000;
    --ink-white: #ffffff;
  }
  html, body {
    margin: 0;
    padding: 0;
    width: 960px;
    height: 1200px;
    overflow: hidden;
    background: var(--pack-black);
  }
  .pack-face {
    position: relative;
    width: 960px;
    height: 1200px;
    background: var(--pack-black);
    color: var(--ink-white);
    font-family: "Tinos", "Times New Roman", serif;
    overflow: hidden;
  }
  .pack-face > * {
    position: absolute;
    left: 0;
    width: 100%;
    margin: 0;
    text-align: center;
    line-height: 1;
    white-space: nowrap;
  }
  .size-label {
    top: 276px;
    font-size: 50px;
    font-weight: 400;
  }
  .size-length {
    top: 348px;
    font-size: 61px;
    font-weight: 700;
  }
  .brand-name {
    top: 521px;
    font-size: 155px;
    font-weight: 700;
  }
  .product-name {
    top: 768px;
    font-size: 89px;
    font-weight: 700;
  }
  .spec-line {
    font-size: 38px;
    font-weight: 400;
  }
  .spec-line--cri { top: 964px; }
  .spec-line--temp { top: 1034px; }
</style>
</head>
<body>
  <main class="pack-face">
    <p class="size-label">Extra Large</p>
    <p class="size-length">5 meters</p>
    <h1 class="brand-name">Lumora</h1>
    <h2 class="product-name">Bias Lighting</h2>
    <p class="spec-line spec-line--cri">Simulated D65 CRI 90+</p>
    <p class="spec-line spec-line--temp">6500K White Bias Lighting</p>
  </main>
</body>
</html>
```